Verodex business card

Business card for sustainable investment company called "Verodex". Verodex is an exchange platform selling carbon credits between buyers and sellers. Carbon Credits are an environmental commodity for reducing global carbon emissions.

the card should obviously have our logo and the theme should be sustainability/environment mixed with a trading platform.

Contact Information for Business Card

Logo, Name, Title, Phone, Email

Colors
0054AA
0677BA
7BADD7
CADEEF
E8F1F8
0094D4
00A9DD
6FCCEA
C7EBF8
E9F6FB
00AB8E
00BBA5
67D7C9
C6EFE9
E9F9F6
59FF00
82FF00
B8FF75
E3FFCB
F4FFEA

```html
<!DOCTYPE html>
<html lang="en">
<head>
<meta charset="utf-8">
<title>Verodex business card</title>
<link href="https://fonts.googleapis.com/css2?family=Montserrat:wght@600;700&family=Source+Sans+3:wght@400&display=swap" rel="stylesheet">
<style>
  :root {
    --canvas-bg: #e4e4e3;
    --navy-dark: #1b2b47;
    --navy-light: #2f4862;
    --paper: #f1f1f2;
    --paper-shade: #e6e6e8;
    --watermark: #dcdde1;
    --ink: #1f2c4a;
    --accent: #3d8fc6;
    --accent-teal: #52b6c8;
    --white: #f4f5f7;
  }
  * { margin: 0; padding: 0; box-sizing: border-box; }
  html, body { width: 1200px; height: 1200px; overflow: hidden; }
  body {
    background: var(--canvas-bg);
    position: relative;
    font-family: "Source Sans 3", "Helvetica Neue", Arial, sans-serif;
  }
  .card {
    position: absolute;
    left: 234px;
    width: 731px;
    height: 417px;
    overflow: hidden;
  }
  .card--front {
    top: 160px;
    background: linear-gradient(225deg, var(--navy-light) 0%, var(--navy-dark) 70%);
    display: flex;
    align-items: center;
    justify-content: center;
  }
  .brand {
    display: flex;
    align-items: center;
    gap: 22px;
    margin-top: -22px;
  }
  .brand__mark {
    width: 46px;
    height: 46px;
    border-radius: 50%;
    background: var(--accent);
  }
  .brand__name {
    font-family: "Montserrat", "Helvetica Neue", Arial, sans-serif;
    font-weight: 600;
    font-size: 56px;
    letter-spacing: 0.5px;
    color: var(--white);
    line-height: 1;
  }
  .card--back {
    top: 632px;
    background: linear-gradient(200deg, var(--paper) 0%, var(--paper-shade) 100%);
  }
  .card__decor {
    position: absolute;
    left: 0;
    top: 0;
    width: 300px;
    height: 100%;
    background: linear-gradient(90deg, var(--watermark) 0%, rgba(220,221,225,0.35) 100%);
  }
  .contact {
    position: absolute;
    left: 354px;
    top: 76px;
    color: var(--ink);
  }
  .contact__name {
    font-family: "Montserrat", "Helvetica Neue", Arial, sans-serif;
    font-weight: 700;
    font-size: 31px;
    line-height: 1;
    background: linear-gradient(90deg, var(--accent-teal), var(--accent));
    -webkit-background-clip: text;
    background-clip: text;
    color: transparent;
  }
  .contact__title {
    font-size: 19px;
    margin-top: 8px;
  }
  .contact__address {
    font-size: 19px;
    line-height: 27px;
    margin-top: 58px;
  }
  .contact__list {
    list-style: none;
    margin-top: 9px;
    font-size: 19px;
    line-height: 28px;
  }
  .contact__list li {
    display: flex;
    align-items: center;
    gap: 7px;
  }
  .contact__icon { width: 15px; height: 15px; flex: none; }
</style>
</head>
<body>
  <section class="card card--front">
    <div class="brand">
      <span class="brand__mark"></span>
      <span class="brand__name">VERODEX</span>
    </div>
  </section>

  <section class="card card--back">
    <div class="card__decor" role="img" aria-label="Faint large brand symbol decoration"></div>
    <div class="contact">
      <h1 class="contact__name">Mark Halden</h1>
      <p class="contact__title">Sales Representative</p>
      <p class="contact__address">Verodex Head Office<br>Budapest XIII. Fenyves utca 12.</p>
      <ul class="contact__list">
        <li>
          <svg class="contact__icon" viewBox="0 0 16 16" aria-hidden="true">
            <path d="M4 1.5l2.2 3-1.3 1.6c.8 1.8 2.3 3.3 4.1 4.1l1.6-1.3 3 2.2-1.2 2.6C7.5 13.7 2.3 8.5 1.5 3.7z" fill="var(--accent)"/>
          </svg>
          +36 30 555 0142
        </li>
        <li>
          <svg class="contact__icon" viewBox="0 0 16 16" aria-hidden="true">
            <rect x="1" y="3" width="14" height="10" fill="var(--accent)"/>
            <path d="M1 3l7 5.5L15 3" fill="none" stroke="#fff" stroke-width="1.2"/>
          </svg>
          szerviz@verodex.com
        </li>
        <li>
          <svg class="contact__icon" viewBox="0 0 16 16" aria-hidden="true">
            <circle cx="8" cy="8" r="6.8" fill="var(--accent)"/>
            <path d="M1.2 8h13.6M8 1.2v13.6M8 1.2c-3 3.5-3 10 0 13.6M8 1.2c3 3.5 3 10 0 13.6" fill="none" stroke="#fff" stroke-width="0.9"/>
          </svg>
          www.verodex.com
        </li>
      </ul>
    </div>
  </section>
</body>
</html>
```